Harbourline Electrical Solutions

On one side. LOGO (underneath:) Commercial Industrial Residential

- NAME & CONTACT DETAILS

Marcus T. Hollings
Project Manager

(Cell icon) (441) 555-0187
(Email icon) hlelectricalsolutions@mailvento.com
(Facebook & Instagram icons )@hlelectricalsolutions

Other side: LOGO - underneath ELECTRICAL CONSTRUCTION & MAINTENANCE . LED LIGHTING & AUTOMATION . LIFE SAFETY SYSTEMS (FIRE ALARM / SECURITY) . DATA & COMMUNICATION

```html
<!DOCTYPE html>
<html lang="en">
<head>
<meta charset="utf-8">
<title>Harbourline Electrical Solutions – Business Card</title>
<link rel="stylesheet" href="https://fonts.googleapis.com/css2?family=Poppins:wght@400;500;600;700&display=swap">
<style>
  :root {
    --teal: #12536a;
    --teal-dark: #0e4557;
    --ink: #3f3f3f;
    --grey: #5a5a5a;
    --paper: #ffffff;
    --stage: #e6e8ea;
  }
  * { box-sizing: border-box; margin: 0; padding: 0; }
  html, body { width: 1200px; height: 1189px; overflow: hidden; }
  body {
    background: var(--stage);
    font-family: "Poppins", Arial, sans-serif;
    display: flex;
    flex-direction: column;
    align-items: center;
    justify-content: center;
    gap: 52px;
  }
  .card {
    width: 900px;
    height: 514px;
    border-radius: 34px;
    position: relative;
    box-shadow: 0 6px 22px rgba(0,0,0,.14);
    overflow: hidden;
  }

  /* Back side */
  .card--back {
    background: var(--teal);
    color: var(--paper);
    display: flex;
    flex-direction: column;
    align-items: center;
    justify-content: center;
    gap: 56px;
  }
  .brand {
    display: flex;
    align-items: center;
    gap: 26px;
  }
  .brand__mark {
    width: 22px; height: 22px;
    border-radius: 50%;
    background: currentColor;
    flex: none;
  }
  .brand__name {
    font-weight: 600;
    text-transform: uppercase;
    letter-spacing: .14em;
    line-height: 1.12;
  }
  .card--back .brand__name { font-size: 40px; }
  .services {
    text-align: center;
    font-size: 17px;
    font-weight: 500;
    line-height: 1.7;
    letter-spacing: .01em;
  }

  /* Front side */
  .card--front {
    background: var(--paper);
    color: var(--ink);
    padding: 74px 70px 0 80px;
  }
  .card--front .brand { color: var(--teal); gap: 20px; }
  .card--front .brand__name { font-size: 34px; }
  .tagline {
    margin: 12px 0 0 42px;
    font-size: 20px;
    font-weight: 500;
    color: var(--grey);
    letter-spacing: .04em;
  }
  .person {
    margin: 44px 0 0 330px;
  }
  .person__name {
    font-size: 27px;
    font-weight: 700;
    color: var(--teal);
    text-transform: uppercase;
    letter-spacing: .02em;
  }
  .person__role {
    font-size: 21px;
    font-weight: 500;
    color: var(--grey);
    margin-top: -2px;
  }
  .contacts {
    list-style: none;
    margin: 34px 0 0 330px;
    font-size: 19px;
    font-weight: 500;
    color: var(--ink);
  }
  .contacts li {
    display: flex;
    align-items: center;
    gap: 12px;
    margin-bottom: 8px;
  }
  .icon {
    width: 28px; height: 28px;
    border-radius: 50%;
    background: var(--teal);
    display: inline-flex;
    align-items: center;
    justify-content: center;
    flex: none;
  }
  .icon svg { width: 16px; height: 16px; }
  .social-dot {
    width: 28px; height: 28px;
    border-radius: 50%;
    background: var(--teal);
    flex: none;
  }
</style>
</head>
<body>

  <section class="card card--back" aria-label="Card back">
    <div class="brand">
      <span class="brand__mark"></span>
      <div class="brand__name">Harbourline<br>Electrical<br>Solutions</div>
    </div>
    <p class="services">
      Electrical Construction &amp; Maintenance | LED Lighting &amp; Automation<br>
      Life Safety Systems (FIRE ALARM / SECURITY) | Data &amp; Communication
    </p>
  </section>

  <section class="card card--front" aria-label="Card front">
    <div class="brand">
      <span class="brand__mark"></span>
      <div class="brand__name">Harbourline<br>Electrical<br>Solutions</div>
    </div>
    <p class="tagline">Commercial Industrial Residential</p>

    <div class="person">
      <h1 class="person__name">Marcus T. Hollings</h1>
      <p class="person__role">Project Manager</p>
    </div>

    <ul class="contacts">
      <li>
        <span class="icon">
          <svg viewBox="0 0 16 16" aria-hidden="true">
            <rect x="4" y="1.5" width="8" height="13" rx="1.6" fill="none" stroke="#fff" stroke-width="1.6"/>
            <circle cx="8" cy="12" r=".9" fill="#fff"/>
          </svg>
        </span>
        (441) 555-0187
      </li>
      <li>
        <span class="icon">
          <svg viewBox="0 0 16 16" aria-hidden="true">
            <rect x="1.5" y="3.5" width="13" height="9" rx="1" fill="none" stroke="#fff" stroke-width="1.5"/>
            <path d="M2 4.5 L8 9 L14 4.5" fill="none" stroke="#fff" stroke-width="1.5"/>
          </svg>
        </span>
        hlelectricalsolutions@mailvento.com
      </li>
      <li>
        <span class="social-dot"></span>
        <span class="social-dot"></span>
        @hlelectricalsolutions
      </li>
    </ul>
  </section>

</body>
</html>
```